New Organic Skin Care Line Needs to Design a Product Label

***THE WINNER OF THIS PROJECT WILL MOST LIKELY BECOME THE EXCLUSIVE DESIGNER FOR OUR OTHER PRODUCT LABELS***

We need a label design for a new organic skin care product line called "Maple Dew Gala." This specific product is a 100% pure organic coconut oil. It's used for skin hydration, protection, and makeup removal.

Info to include on front label:

1. Logo: Maple Dew Gala (attached)
2. Product Name: Pure Coconut Oil (emphasize "organic" somewhere)
3. Slogan: Hydrate your skin and hair.
4. Size: 8 FL OZ 236mL

Attached is:

1. The brand logo "Maple Dew Gala" with a white background.
2. An image of the bottle we will use.
3. An image of the bottle with lines to show the size and placement of the label.
4. The brand logo "Maple Dew Gala" with a black background. (photoshop file)

What we need:

A simple mock up of the front side of the label on the bottle. We first want to know what it will look like on the bottle given the size and dimensions.

- We would like one label with a white background (including the logo with a white background).
- We would like a second label with a black background (including the logo with a black background, just need to make the black font white instead of black).

We can get a great idea of what to expect from the front side of the label so we will complete the back side once we identify a winner.
Updates

Apologies, but we are now using a different bottle. The previous one is now discontinued. Please view the two most recent images uploaded. One is an image of the new bottle by itself. The other is an image of that bottle with instructions. Please use your most recent designs on the new bottle. Feel free to make any modifications you see fit to compliment the new bottle shape. Added Friday, March 18, 2016

Reason: We are still working with the label company to finalize the size. Once the size is confirmed we will have to tweak labels based on finalized measurements.

Target Market(s)

Women, 18-70

Industry/Entity Type

Skin Care Product

Font styles to use
Decorative
Script

Requirements
Must have
• -"shabby sheek" and "cute" theme
• -soft organic feel
• -the ingredients are organic, pure, and natural. That should be an essence of the label.

```html
<!DOCTYPE html>
<html lang="en">
<head>
<meta charset="utf-8">
<title>Maple Dew Gala — Pure Coconut Oil Label</title>
<link rel="stylesheet" href="https://fonts.googleapis.com/css2?family=Cinzel:wght@600&family=Marcellus&family=Open+Sans:wght@500&family=Playfair+Display:ital@1&display=swap">
<style>
  :root {
    --paper: #ffffff;
    --edge: #333333;
    --dot-yellow: #ede37c;
    --leaf-green: #2f8d57;
    --band-green: #3fae49;
    --pill-green: #3d9a4a;
    --gold: #b8862b;
    --tan: #a89a6a;
    --white: #ffffff;
  }
  html, body {
    margin: 0;
    padding: 0;
    overflow: hidden;
    background: var(--paper);
  }
  .label {
    position: relative;
    width: 1200px;
    height: 1091px;
    box-sizing: border-box;
    border: 1px solid var(--edge);
    background: var(--paper);
    overflow: hidden;
  }
  .label-art {
    position: absolute;
    inset: 0;
    width: 100%;
    height: 100%;
  }
  .dotted-frame {
    fill: none;
    stroke: var(--dot-yellow);
    stroke-width: 14;
    stroke-dasharray: 14 14;
  }
  .brand-name {
    font-family: "Marcellus", serif;
    font-size: 22px;
    letter-spacing: 5.5px;
    fill: var(--tan);
  }
  .product-name {
    font-family: "Cinzel", serif;
    font-weight: 600;
    font-size: 62px;
    fill: var(--leaf-green);
  }
  .organic-band { fill: var(--band-green); }
  .organic-word {
    font-family: "Open Sans", sans-serif;
    font-weight: 500;
    font-size: 40px;
    letter-spacing: 1px;
    fill: var(--white);
  }
  .slogan {
    font-family: "Marcellus", serif;
    font-size: 48px;
    fill: var(--gold);
  }
  .illustration { fill: url(#coconut-tones); }
  .size-pill { fill: var(--pill-green); }
  .size-text {
    font-family: "Playfair Display", serif;
    font-style: italic;
    font-size: 44px;
    fill: var(--white);
  }
</style>
</head>
<body>
<main class="label">
  <svg class="label-art" viewBox="0 0 1200 1091" xmlns="http://www.w3.org/2000/svg">
    <defs>
      <path id="title-arc" d="M260,620 A340,340 0 0 1 940,620"/>
      <radialGradient id="coconut-tones" cx="50%" cy="45%" r="55%">
        <stop offset="0%" stop-color="#6b3b1f"/>
        <stop offset="45%" stop-color="#8a6a4a"/>
        <stop offset="75%" stop-color="#6fbf4a"/>
        <stop offset="100%" stop-color="#a8dc8a"/>
      </radialGradient>
    </defs>

    <path class="dotted-frame" d="M600,14 C780,14 1010,200 1120,330 C1180,400 1188,480 1188,545 C1188,610 1180,690 1120,760 C1010,890 780,1078 600,1078 C420,1078 190,890 80,760 C20,690 12,610 12,545 C12,480 20,400 80,330 C190,200 420,14 600,14 Z"/>

    <text class="brand-name" x="600" y="199" text-anchor="middle">MAPLE DEW GALA</text>

    <text class="product-name">
      <textPath href="#title-arc" startOffset="50%" text-anchor="middle" textLength="760" lengthAdjust="spacing">PURE COCONUT OIL</textPath>
    </text>

    <path class="organic-band" d="M412,330 L800,330 L836,374 L372,374 Z"/>
    <text class="organic-word" x="608" y="368" text-anchor="middle">ORGANIC</text>

    <text class="slogan" x="608" y="466" text-anchor="middle">HYDRATE</text>
    <text class="slogan" x="610" y="518" text-anchor="middle">YOUR SKIN AND HAIR.</text>

    <ellipse class="illustration" cx="594" cy="726" rx="266" ry="172" role="img" aria-label="Illustration of halved coconuts with white plumeria flowers on a spray of green palm fronds"/>

    <ellipse class="size-pill" cx="606" cy="952" rx="84" ry="38"/>
    <text class="size-text" x="606" y="967" text-anchor="middle">236ml</text>
  </svg>
</main>
</body>
</html>
```